LB - WESITE NEEDED PAGE: Clean / Modern / Pro & Dynamic

Lantern-Brokers is a new insurance brokerage firm dealing exclusively with companies (BToB) providing the following property: Liabilities Insurance Insurances Automobile Insurance Insurances Construction% 26amp; Engineering Casualty Workmen 's Compensation Health Insurance Marime% 26amp; Transit Credit Insurance Young, Fast, Proactive and Dynamic we call ourselves Lantern-Brokers because we are a "start-up" willing to make a difference in the market, bringing modernity and speed to our industry, still too bureaucratic / procedural / opaque uninitiated. We need something respecting the colors of our orange logtype; blue; white; black; easy to scroll, with simple information on the company; - who we are - our team (with the pictures) - what we do - what we do - contact us, contact us (google map) Luanda (Angola) Small company, just need something flashy / professional / structured / modern.

Target Market(s)

BtoB; Oil and gas companies; French speaking copying established in Angola, all industrials, factories and importers of goods.

Industry/Entity Type

Insurance Broker

Font styles to use
Sans Serif

Colors

Designer to choose colors to be used in the design.

Requirements
Must have
• We need something respecting the colors of our orange logtype; blue; white; black; easy to scroll, with simple information on the company; - who we are - our team (with the pictures) - what we do - what we do - contact us, contact us (google map) Luanda (Angola) Small company, just need something flashy / professional / structured / modern.
Nice to have
• A page format
Should not have
• WE DO NOT WANT A REFER TO OUR LOGO, but a Home Page for our Website with the basics categories ... >> PLEASE CAREFULLY USE THE RIGHT COLOR OF THE LOGOTYPE which are the ones enclosed Orange / Turquoise / Black as per the business card .

```html
<!DOCTYPE html>
<html lang="en">
<head>
<meta charset="utf-8">
<title>Lantern-Brokers — Insurance Brokerage</title>
<link rel="stylesheet" href="https://fonts.googleapis.com/css2?family=Montserrat:wght@400;600;700;800&family=Open+Sans:wght@400;600;700&display=swap">
<style>
:root{
  --orange:#f05a28;
  --orange-deep:#e2382b;
  --blue:#1c8fe0;
  --blue-deep:#1570c7;
  --ink:#1f1f1f;
  --text:#555;
  --muted:#8a8a8a;
  --line:#e4e4e4;
  --white:#fff;
  --soft:#f6f6f6;
}
*{box-sizing:border-box;margin:0;padding:0}
html,body{width:1200px;height:3692px;overflow:hidden}
body{font-family:"Open Sans",Arial,sans-serif;color:var(--text);background:var(--white);font-size:15px;line-height:1.6;position:relative}
h1,h2,h3,h4,.nav,.brand{font-family:"Montserrat",Arial,sans-serif}
.section-title{font-size:38px;font-weight:800;color:var(--ink);text-align:center;letter-spacing:1px}
.title-mark{display:flex;justify-content:center;align-items:center;gap:10px;margin:10px 0 0}
.title-mark span{width:60px;height:2px;background:var(--line)}
.title-mark i{width:12px;height:12px;border:2px solid var(--orange);border-radius:50%}

/* header */
.site-header{position:absolute;top:0;left:0;width:1200px;height:72px;background:var(--white);display:flex;align-items:center;padding:0 40px;z-index:3;box-shadow:0 2px 6px rgba(0,0,0,.06)}
.brand{display:flex;align-items:center;gap:10px;font-weight:800;font-size:20px;color:var(--orange);letter-spacing:.5px}
.brand-dot{width:24px;height:24px;border-radius:50%;background:var(--orange)}
.header-right{margin-left:auto;display:flex;flex-direction:column;align-items:flex-end;gap:6px}
.contact-line{display:flex;gap:24px;font-size:12px;color:var(--muted)}
.contact-line span{display:flex;align-items:center;gap:6px}
.nav{display:flex;gap:4px;font-size:12px;font-weight:700;color:var(--ink)}
.nav a{padding:5px 14px;text-decoration:none;color:inherit}
.nav a.active{background:var(--orange);color:var(--white)}

/* hero */
.hero{position:absolute;top:72px;left:0;width:1200px;height:528px;overflow:hidden}
.hero-photo{position:absolute;inset:0;background:linear-gradient(100deg,#cfc6bb 0%,#e9e1d6 30%,#f2ece4 55%,#c9c1b7 100%)}
.hero-copy{position:absolute;right:40px;top:300px;text-align:right}
.hero-copy h1{font-size:40px;font-weight:800;color:var(--orange);line-height:1.15;text-transform:uppercase}
.hero-band{margin-top:12px;display:inline-block;background:rgba(20,20,20,.72);padding:10px 18px;color:var(--white);font-family:"Montserrat",sans-serif;font-weight:700;font-size:17px;line-height:1.4;text-transform:uppercase;text-align:right}
.hero-dots{position:absolute;right:40px;bottom:40px;display:flex;gap:8px}
.hero-dots i{width:12px;height:12px;border-radius:50%;border:2px solid var(--white)}
.hero-dots i.on{background:var(--orange);border-color:var(--orange)}

/* who we are */
.who{position:absolute;top:600px;left:0;width:1200px;height:448px;display:flex;align-items:center;padding:0 140px;gap:70px}
.who-name{width:300px;display:flex;align-items:center;justify-content:center;font-family:"Montserrat",sans-serif;font-weight:800;font-size:26px;color:var(--orange);letter-spacing:.5px}
.who-copy{flex:1}
.who-copy h2{font-size:36px;font-weight:800;color:var(--ink);letter-spacing:1px}
.who-copy .rule{width:60px;height:3px;background:var(--orange);margin:12px 0 20px}
.who-copy .lead{font-weight:700;color:var(--ink);font-size:17px;margin-bottom:14px}

/* what we do */
.what{position:absolute;top:1048px;left:0;width:1200px;height:520px;overflow:hidden;color:var(--white);text-align:center}
.what-photo{position:absolute;inset:0;background:linear-gradient(90deg,#2b2622 0%,#4a3d34 40%,#3a332e 70%,#221f1c 100%)}
.what-shade{position:absolute;inset:0;background:rgba(15,15,15,.55)}
.what-inner{position:relative;padding-top:70px}
.what .section-title{color:var(--white)}
.what .intro{width:560px;margin:22px auto 40px;font-size:14px;color:#e8e8e8}
.services{display:flex;justify-content:center;gap:70px}
.service{width:240px}
.service svg{width:64px;height:64px;margin-bottom:12px}
.service h3{font-size:14px;font-weight:700;letter-spacing:.5px;margin-bottom:8px}
.service p{font-size:13px;color:#dcdcdc}
.what .dots{display:flex;justify-content:center;gap:8px;margin-top:30px}
.what .dots i{width:10px;height:10px;border-radius:50%;background:rgba(255,255,255,.5)}
.what .dots i.on{background:var(--blue)}

/* team */
.team{position:absolute;top:1600px;left:0;width:1200px;height:520px;text-align:center}
.team .intro{width:840px;margin:22px auto 40px;font-size:14px}
.team-row{display:flex;justify-content:center;align-items:flex-start;gap:44px}
.lead-card{width:190px;height:330px;background:linear-gradient(160deg,var(--orange) 0%,var(--orange-deep) 100%);color:var(--white);padding:40px 20px;text-align:center;margin-top:-20px;box-shadow:0 8px 20px rgba(0,0,0,.15)}
.lead-card h4{font-size:16px;font-weight:700}
.lead-card .role{font-size:13px;opacity:.85;margin-bottom:12px}
.lead-card p{font-size:12px;line-height:1.5}
.lead-card .arrow{width:36px;height:36px;border-radius:50%;background:var(--white);margin:20px auto 0;display:flex;align-items:center;justify-content:center}
.member{width:150px}
.member .photo{width:140px;height:140px;border-radius:50%;margin:0 auto 14px;background:linear-gradient(160deg,#c9b9a8,#8b7b6d);border:4px solid var(--white);box-shadow:0 4px 12px rgba(0,0,0,.12)}
.member h4{font-size:16px;font-weight:700;color:var(--ink)}
.member .role{font-size:13px;color:var(--muted)}
.member .social{width:26px;height:26px;border-radius:50%;background:var(--blue);margin:10px auto 0}

/* why */
.why{position:absolute;top:2160px;left:0;width:1200px;height:608px;background:var(--soft)}
.why-inner{padding-top:60px}
.why-grid{display:grid;grid-template-columns:repeat(3,300px);gap:36px 40px;justify-content:center;margin-top:44px}
.why-card{height:180px;background:var(--white);box-shadow:0 4px 14px rgba(0,0,0,.08);padding:22px 26px;text-align:center}
.why-card svg{width:50px;height:50px;margin-bottom:8px}
.why-card h4{font-size:14px;font-weight:700;color:var(--ink);letter-spacing:.5px;margin-bottom:6px}
.why-card p{font-size:13px;line-height:1.5}
.why-card.blue{background:linear-gradient(160deg,var(--blue),var(--blue-deep));color:var(--white)}
.why-card.blue h4{color:var(--white)}

/* contact / map */
.talk{position:absolute;top:2768px;left:0;width:1200px;height:584px;overflow:hidden}
.map{position:absolute;inset:0;background:linear-gradient(135deg,#e8ecd8 0%,#dfe6cc 40%,#eef0e2 70%,#d9e2c4 100%)}
.form-card{position:absolute;left:140px;top:90px;width:420px;height:410px;background:var(--white);box-shadow:0 10px 30px rgba(0,0,0,.18);padding:34px 40px}
.form-card h2{font-size:32px;font-weight:800;color:var(--ink)}
.form-card .rule{width:50px;height:3px;background:var(--orange);margin:8px 0 22px}
.field{height:40px;border-bottom:1px solid var(--line);display:flex;align-items:center;gap:10px;font-size:13px;color:var(--muted);margin-bottom:8px}
.field i{width:8px;height:8px;border-radius:50%;background:var(--orange)}
.submit{margin-top:24px;display:inline-block;background:var(--ink);color:var(--white);font-family:"Montserrat",sans-serif;font-weight:700;font-size:13px;padding:12px 30px}
.pin{position:absolute;left:800px;top:215px}
.address-card{position:absolute;left:760px;top:258px;width:300px;background:var(--white);box-shadow:0 4px 14px rgba(0,0,0,.15);padding:14px 16px;font-size:12px;line-height:1.5;color:var(--ink);display:flex;align-items:center;gap:12px}
.address-card .dot{width:28px;height:28px;border-radius:50%;background:var(--orange);flex:none}

/* footer */
.site-footer{position:absolute;top:3352px;left:0;width:1200px;height:340px;overflow:hidden;color:var(--white);text-align:center}
.footer-bg{position:absolute;inset:0;background:linear-gradient(180deg,var(--orange) 0%,var(--orange-deep) 100%)}
.footer-inner{position:relative;padding-top:34px}
.footer-brand{display:inline-flex;align-items:center;gap:10px;font-family:"Montserrat",sans-serif;font-weight:800;font-size:20px}
.footer-brand i{width:22px;height:22px;border-radius:50%;background:var(--white)}
.footer-cols{display:flex;justify-content:center;gap:170px;margin-top:40px}
.footer-col{width:200px;font-size:13px}
.footer-col svg{width:34px;height:34px;margin-bottom:6px}
.footer-col h4{font-size:14px;font-weight:700;letter-spacing:1px}
.footer-bottom{position:absolute;left:0;bottom:0;width:1200px;height:56px;background:rgba(0,0,0,.18);display:flex;align-items:center;justify-content:space-between;padding:0 140px;font-size:12px}
.socials{display:flex;gap:10px}
.socials i{width:26px;height:26px;border-radius:50%;border:2px solid var(--white)}
</style>
</head>
<body>

<header class="site-header">
  <div class="brand"><span class="brand-dot"></span>LANTERN-BROKERS</div>
  <div class="header-right">
    <div class="contact-line">
      <span><svg width="12" height="12" viewBox="0 0 24 24"><path d="M6 2l4 4-2 3a12 12 0 007 7l3-2 4 4-3 4C10 22 2 14 2 5z" fill="#f05a28"/></svg>+244 900 000 000</span>
      <span><svg width="12" height="12" viewBox="0 0 24 24"><rect x="2" y="5" width="20" height="14" fill="none" stroke="#f05a28" stroke-width="2"/><path d="M2 6l10 7 10-7" fill="none" stroke="#f05a28" stroke-width="2"/></svg>hello@lanternbrokers.co</span>
    </div>
    <nav class="nav">
      <a class="active">HOME</a><a>WHO WE ARE</a><a>WHAT WE DO</a><a>OUR TEAM</a><a>CONTACT US</a>
    </nav>
  </div>
</header>

<section class="hero">
  <div class="hero-photo" role="img" aria-label="Business person standing at an office window overlooking a city skyline"></div>
  <div class="hero-copy">
    <h1>Young, Fast,<br>Proactive &amp; Dynamic</h1>
    <div class="hero-band">We are insurance brokerage firm<br>dealing exclusively with companies</div>
  </div>
  <div class="hero-dots"><i class="on"></i><i></i><i></i></div>
</section>

<section class="who">
  <div class="who-name">LANTERN-BROKERS</div>
  <div class="who-copy">
    <h2>WHO WE ARE</h2>
    <div class="rule"></div>
    <p class="lead">A young brokerage firm built to bring speed, clarity and modern service to business insurance.</p>
    <p>We work only with companies, from oil and gas operators to factories and importers. Our team compares the market for you, explains every clause in plain words and stays beside you when a claim arrives. No long forms, no hidden steps, just clear advice and quick answers when your business needs them most.</p>
  </div>
</section>

<section class="what">
  <div class="what-photo" role="img" aria-label="Team of business professionals in a meeting"></div>
  <div class="what-shade"></div>
  <div class="what-inner">
    <h2 class="section-title">WHAT WE DO</h2>
    <div class="title-mark"><span></span><i></i><span></span></div>
    <p class="intro">We design insurance programmes for companies, covering people, assets and operations with cover that fits each industry.</p>
    <div class="services">
      <div class="service">
        <svg viewBox="0 0 64 64"><path d="M32 6l22 8v16c0 14-10 24-22 28C20 54 10 44 10 30V14z" fill="none" stroke="#f05a28" stroke-width="3"/><path d="M22 32l7 7 13-14" fill="none" stroke="#fff" stroke-width="3"/></svg>
        <h3>LIABILITIES INSURANCE</h3>
        <p>Protection against third party claims linked to your daily operations.</p>
      </div>
      <div class="service">
        <svg viewBox="0 0 64 64"><path d="M10 40l5-14h34l5 14v10H10z" fill="none" stroke="#f05a28" stroke-width="3"/><circle cx="20" cy="50" r="5" fill="none" stroke="#fff" stroke-width="3"/><circle cx="44" cy="50" r="5" fill="none" stroke="#fff" stroke-width="3"/></svg>
        <h3>AUTOMOBILE INSURANCE</h3>
        <p>Fleet cover for company cars, trucks and service vehicles.</p>
      </div>
      <div class="service">
        <svg viewBox="0 0 64 64"><path d="M32 54S8 40 8 24a12 12 0 0124-6 12 12 0 0124 6c0 16-24 30-24 30z" fill="none" stroke="#f05a28" stroke-width="3"/><path d="M26 30h12M32 24v12" stroke="#fff" stroke-width="3"/></svg>
        <h3>HEALTH INSURANCE</h3>
        <p>Medical plans that look after your staff and their families.</p>
      </div>
    </div>
    <div class="dots"><i class="on"></i><i></i><i></i></div>
  </div>
</section>

<section class="team">
  <h2 class="section-title">OUR TEAM</h2>
  <div class="title-mark"><span></span><i></i><span></span></div>
  <p class="intro">A small team of brokers with deep experience across industrial, energy and trade sectors, ready to answer quickly and follow every file from quote to claim.</p>
  <div class="team-row">
    <div class="lead-card" role="img" aria-label="Portrait of the founder behind an orange overlay">
      <h4>NADIA REYES</h4>
      <div class="role">Founder</div>
      <p>Leads strategy and client relations with fifteen years in corporate insurance.</p>
      <div class="arrow"><svg width="14" height="14" viewBox="0 0 24 24"><path d="M5 12h14M13 6l6 6-6 6" fill="none" stroke="#f05a28" stroke-width="3"/></svg></div>
    </div>
    <div class="member"><div class="photo" role="img" aria-label="Portrait of team member Dario"></div><h4>DARIO</h4><div class="role">Designation</div><div class="social"></div></div>
    <div class="member"><div class="photo" role="img" aria-label="Portrait of team member Milan"></div><h4>MILAN</h4><div class="role">Designation</div><div class="social"></div></div>
    <div class="member"><div class="photo" role="img" aria-label="Portrait of team member Gerald"></div><h4>GERALD</h4><div class="role">Designation</div><div class="social"></div></div>
    <div class="member"><div class="photo" role="img" aria-label="Portrait of team member Henrik"></div><h4>HENRIK</h4><div class="role">Designation</div><div class="social"></div></div>
  </div>
</section>

<section class="why">
  <div class="why-inner">
    <h2 class="section-title">WHY CHOOSE US</h2>
    <div class="title-mark"><span></span><i></i><span></span></div>
    <div class="why-grid">
      <div class="why-card">
        <svg viewBox="0 0 50 50"><circle cx="25" cy="18" r="9" fill="none" stroke="#1c8fe0" stroke-width="2.5"/><path d="M10 44c2-10 28-10 30 0" fill="none" stroke="#1c8fe0" stroke-width="2.5"/></svg>
        <h4>CERTIFIED EXPERTS</h4><p>Licensed brokers who know the local market well.</p>
      </div>
      <div class="why-card blue">
        <svg viewBox="0 0 50 50"><rect x="10" y="8" width="30" height="36" fill="none" stroke="#fff" stroke-width="2.5"/><path d="M17 18h16M17 26h16M17 34h10" stroke="#fff" stroke-width="2.5"/></svg>
        <h4>TAX BENEFITS</h4><p>Structured cover that keeps your costs efficient.</p>
      </div>
      <div class="why-card">
        <svg viewBox="0 0 50 50"><path d="M8 26l4-4 10 10 18-18 4 4-22 22z" fill="none" stroke="#1c8fe0" stroke-width="2.5"/></svg>
        <h4>WORK SATISFACTION</h4><p>Clients stay with us because we keep our word.</p>
      </div>
      <div class="why-card blue">
        <svg viewBox="0 0 50 50"><circle cx="25" cy="27" r="16" fill="none" stroke="#fff" stroke-width="2.5"/><path d="M25 17v10l7 5M20 6h10" fill="none" stroke="#fff" stroke-width="2.5"/></svg>
        <h4>FAST RESPONSE TIME</h4><p>Quotes and answers delivered within one day.</p>
      </div>
      <div class="why-card">
        <svg viewBox="0 0 50 50"><circle cx="15" cy="16" r="6" fill="none" stroke="#1c8fe0" stroke-width="2.5"/><circle cx="35" cy="16" r="6" fill="none" stroke="#1c8fe0" stroke-width="2.5"/><path d="M4 40c2-10 20-10 22 0M24 40c2-10 20-10 22 0" fill="none" stroke="#1c8fe0" stroke-width="2.5"/></svg>
        <h4>FULL SUPPORT</h4><p>One contact follows your file from start to claim.</p>
      </div>
      <div class="why-card blue">
        <svg viewBox="0 0 50 50"><circle cx="25" cy="25" r="17" fill="none" stroke="#fff" stroke-width="2.5"/><path d="M30 18h-7a4 4 0 000 8h4a4 4 0 010 8h-8M25 14v22" fill="none" stroke="#fff" stroke-width="2.5"/></svg>
        <h4>AFFORDABLE PRICE</h4><p>Fair premiums negotiated across many insurers.</p>
      </div>
    </div>
  </div>
</section>

<section class="talk">
  <div class="map" role="img" aria-label="Street map of Luanda with the office location marked"></div>
  <div class="form-card">
    <h2>LET'S TALK</h2>
    <div class="rule"></div>
    <div class="field"><i></i>Name</div>
    <div class="field"><i></i>Phone</div>
    <div class="field"><i></i>Email</div>
    <div class="field"><i></i>Message</div>
    <span class="submit">SUBMIT</span>
  </div>
  <svg class="pin" width="30" height="40" viewBox="0 0 30 40"><path d="M15 0a15 15 0 0115 15c0 11-15 25-15 25S0 26 0 15A15 15 0 0115 0z" fill="#e2382b"/><circle cx="15" cy="15" r="6" fill="#fff"/></svg>
  <div class="address-card"><span class="dot"></span><span>48 Harbour Lane, Marginal District,<br>Luanda, Angola</span></div>
</section>

<footer class="site-footer">
  <div class="footer-bg" role="img" aria-label="City skyline under an orange and red tint"></div>
  <div class="footer-inner">
    <div class="footer-brand"><i></i>LANTERN-BROKERS</div>
    <div class="footer-cols">
      <div class="footer-col">
        <svg viewBox="0 0 34 34"><path d="M17 3a10 10 0 0110 10c0 8-10 18-10 18S7 21 7 13A10 10 0 0117 3z" fill="none" stroke="#fff" stroke-width="2.5"/><circle cx="17" cy="13" r="3.5" fill="#fff"/></svg>
        <h4>ADDRESS</h4><p>48 Harbour Lane, Marginal District, Luanda</p>
      </div>
      <div class="footer-col">
        <svg viewBox="0 0 34 34"><path d="M9 4l6 6-3 4a16 16 0 008 8l4-3 6 6-4 5C14 30 4 20 4 8z" fill="none" stroke="#fff" stroke-width="2.5"/></svg>
        <h4>PHONE</h4><p>+244 900 000 000</p>
      </div>
      <div class="footer-col">
        <svg viewBox="0 0 34 34"><rect x="4" y="8" width="26" height="18" fill="none" stroke="#fff" stroke-width="2.5"/><path d="M4 9l13 9 13-9" fill="none" stroke="#fff" stroke-width="2.5"/></svg>
        <h4>EMAIL</h4><p>hello@lanternbrokers.co</p>
      </div>
    </div>
  </div>
  <div class="footer-bottom">
    <span>Copyright © 2024 Lantern-Brokers. All rights reserved.</span>
    <div class="socials"><i></i><i></i><i></i><i></i></div>
  </div>
</footer>

</body>
</html>
```